Basic business card

use my newly created logo - and the phrases (Lower Cost of Test & Accelarated New Product Introduction) - and my new email domain / ID - use at conferences / tradeshows

Industry/Entity Type

semiconductor

Contact Information for Business Card

Daniel K Forde, Owner, communicate via Logo - Lower COT - Cost of Test, Accelerated NPI - New Product Introduction, phone +1 555 613 0946, Chandler, Arizona, USA, daniel.forde@qal-vub.com

Font styles to use
Sans Serif

Requirements
Nice to have
• re-use my logo created via Pixel Harbor last August (#7315926)

```html
<!DOCTYPE html>
<html lang="en">
<head>
<meta charset="utf-8">
<title>QAL-VUB Business Card</title>
<link href="https://fonts.googleapis.com/css2?family=Open+Sans:wght@400;600;700&display=swap" rel="stylesheet">
<style>
  :root {
    --stage: #222224;
    --card: #1d1e22;
    --brand-blue: #0b72b9;
    --brand-orange: #f0961e;
    --logo-grey: #5b6477;
    --back-mark: #2c2d33;
    --ink-light: #ffffff;
  }
  html, body {
    margin: 0;
    width: 1200px;
    height: 779px;
    overflow: hidden;
    background: var(--stage);
    font-family: "Open Sans", sans-serif;
  }
  .stage {
    width: 1200px;
    height: 779px;
    display: flex;
    align-items: center;
    justify-content: center;
    gap: 40px;
  }
  .card {
    position: relative;
    width: 540px;
    height: 309px;
    background: var(--card);
    overflow: hidden;
  }
  .card-wave {
    position: absolute;
    inset: 0;
  }
  .brand-name {
    position: absolute;
    left: 34px;
    top: 26px;
    margin: 0;
    font-size: 30px;
    font-weight: 400;
    letter-spacing: 1px;
    color: var(--logo-grey);
  }
  .holder {
    position: absolute;
    right: 26px;
    top: 118px;
    text-align: right;
  }
  .holder-name {
    margin: 0;
    font-size: 25px;
    font-weight: 700;
    line-height: 1.1;
  }
  .holder-name .first { color: var(--brand-orange); }
  .holder-name .last { color: var(--brand-blue); }
  .holder-title {
    margin: 4px 0 0;
    font-size: 12px;
    color: var(--ink-light);
  }
  .contact {
    position: absolute;
    right: 130px;
    top: 222px;
    margin: 0;
    padding: 0;
    list-style: none;
    text-align: right;
    color: var(--ink-light);
    font-size: 11.5px;
    line-height: 15px;
  }
  .contact li { display: flex; justify-content: flex-end; align-items: center; gap: 6px; }
  .contact .icon { width: 10px; height: 10px; fill: var(--ink-light); }
  .contact .spacer { width: 10px; }
  .card-back {
    display: flex;
    align-items: center;
    justify-content: center;
  }
  .back-mark {
    margin: 0;
    font-size: 52px;
    font-weight: 400;
    letter-spacing: 2px;
    color: var(--back-mark);
  }
</style>
</head>
<body>
<main class="stage">
  <section class="card card-front">
    <svg class="card-wave" viewBox="0 0 540 309" aria-hidden="true">
      <path d="M0,170 C30,240 150,245 270,215 C380,190 440,230 470,309 L0,309 Z" fill="var(--brand-blue)"/>
      <path d="M22,140 C45,215 150,225 270,203 C370,185 420,200 448,235" fill="none" stroke="var(--brand-orange)" stroke-width="5"/>
      <path d="M540,270 L540,309 L505,309 Z" fill="var(--brand-blue)"/>
    </svg>
    <h1 class="brand-name">QAL-VUB</h1>
    <div class="holder">
      <p class="holder-name"><span class="first">Lena</span> <span class="last">Marsh</span></p>
      <p class="holder-title">Managing Director</p>
    </div>
    <ul class="contact">
      <li>740 Orchard Ln. Suite 310<span class="spacer"></span></li>
      <li>Chandler, AZ 85225<span class="spacer"></span></li>
      <li>(555) 214-3087
        <svg class="icon" viewBox="0 0 10 10"><path d="M2,0.5 L4,2.5 L3,4 C3.6,5.3 4.7,6.4 6,7 L7.5,6 L9.5,8 L8,9.5 C4,9.5 0.5,6 0.5,2 Z"/></svg></li>
      <li>hello@qal-vub.com
        <svg class="icon" viewBox="0 0 10 10"><path d="M0.5,2 H9.5 V8 H0.5 Z M1,2.5 L5,5.5 L9,2.5" stroke="var(--brand-blue)" stroke-width="0.8"/></svg></li>
      <li>www.qal-vub.com
        <svg class="icon" viewBox="0 0 10 10"><circle cx="5" cy="5" r="4.5"/><path d="M0.5,5 H9.5 M5,0.5 C2.5,3 2.5,7 5,9.5 M5,0.5 C7.5,3 7.5,7 5,9.5" fill="none" stroke="var(--brand-blue)" stroke-width="0.7"/></svg></li>
    </ul>
  </section>
  <section class="card card-back">
    <p class="back-mark">QAL-VUB</p>
  </section>
</main>
</body>
</html>
```